Clear sticker design for packaging

I need 4” diameter clear stickers designed for birthdays, thank you , teachers day and all the other special days to complete my gift packaging. They will go on the top of each tube to differentiate each gift for each occasion. Our design is on craft paper and I’ve uploaded a few examples of what we are trying to achieve. Last picture is the top of our tube where the stickers will be placed. We don’t want too much color unless for Christmas and Valentine’s Day maybe! We are working with black and gold or a mixture of both mostly

```html
<!DOCTYPE html>
<html lang="en">
<head>
<meta charset="utf-8">
<title>Occasion Sticker Set</title>
<link rel="stylesheet" href="https://fonts.googleapis.com/css2?family=Playfair+Display:ital,wght@1,900&display=swap">
<style>
  :root {
    --kraft: #d7b57c;
    --sticker: #ffffff;
    --line: #6f6f6f;
    --ornament: #e6e6e6;
    --gold: #d9ad12;
    --gold-edge: #6d5a06;
  }
  * { margin: 0; padding: 0; box-sizing: border-box; }
  html, body { width: 848px; height: 1200px; overflow: hidden; }
  body { background: var(--kraft); position: relative; }
  .sticker {
    position: absolute;
    width: 280px; height: 280px;
    border-radius: 50%;
    background: var(--sticker);
    overflow: hidden;
  }
  .sticker svg { position: absolute; inset: 0; width: 280px; height: 280px; }
  .frame { fill: none; stroke: var(--line); stroke-width: 1.4; }
  .ornament { fill: none; stroke: var(--ornament); stroke-width: 14; stroke-linecap: round; }
  .greeting {
    position: absolute;
    left: 0; right: 0;
    text-align: center;
    font-family: "Playfair Display", serif;
    font-style: italic;
    font-weight: 900;
    text-transform: uppercase;
    color: var(--gold);
    letter-spacing: -0.5px;
    line-height: 0.95;
    white-space: nowrap;
    -webkit-text-stroke: 0.8px var(--gold-edge);
    text-shadow: 2px 2px 0 var(--gold-edge);
  }
  .christmas   { left: 93px;  top: 94px; }
  .teachers    { left: 447px; top: 91px; }
  .thanks      { left: 93px;  top: 446px; }
  .birthday    { left: 447px; top: 446px; }
  .mothers     { left: 93px;  top: 802px; }
  .anniversary { left: 447px; top: 802px; }
</style>
</head>
<body>

<div class="sticker christmas">
  <svg viewBox="0 0 280 280">
    <circle class="ornament" role="img" aria-label="Leafy wreath encircling the greeting" cx="140" cy="140" r="112"/>
  </svg>
  <div class="greeting" style="top:108px;font-size:30px;">Merry<br>Christmas</div>
</div>

<div class="sticker teachers">
  <svg viewBox="0 0 280 280">
    <circle class="frame" cx="150" cy="140" r="116"/>
    <path class="ornament" role="img" aria-label="Trailing leaf sprig along the lower left"
      d="M46 80A116 116 0 0 0 170 254"/>
  </svg>
  <div class="greeting" style="top:102px;font-size:29px;">Happy<br>Teacher’s<br>Day</div>
</div>

<div class="sticker thanks">
  <svg viewBox="0 0 280 280">
    <circle class="frame" cx="140" cy="142" r="124"/>
    <circle class="frame" cx="140" cy="142" r="120"/>
    <path class="ornament" role="img" aria-label="Small flower and leaf sprig at the lower left"
      d="M52 222A120 120 0 0 0 130 262"/>
  </svg>
  <div class="greeting" style="top:104px;font-size:42px;">Thank<br>You</div>
</div>

<div class="sticker birthday">
  <svg viewBox="0 0 280 280">
    <circle class="frame" cx="146" cy="146" r="110"/>
    <circle class="frame" cx="146" cy="148" r="114"/>
    <path class="ornament" role="img" aria-label="Curling vine on the left side"
      d="M62 60A114 114 0 0 0 44 200"/>
    <path class="ornament" role="img" aria-label="Curling vine on the right side"
      d="M240 90A114 114 0 0 1 254 180"/>
  </svg>
  <div class="greeting" style="top:116px;font-size:27px;">Happy<br>Birthday</div>
</div>

<div class="sticker mothers">
  <svg viewBox="0 0 280 280">
    <path class="frame" d="M43 119A115 115 0 0 1 266 159V190"/>
    <path class="ornament" role="img" aria-label="Blossom with leafy branches at the lower left"
      d="M30 130Q30 200 70 230Q100 252 140 256"/>
  </svg>
  <div class="greeting" style="top:100px;font-size:29px;padding-left:34px;">Happy<br>Mother’s<br>Day</div>
</div>

<div class="sticker anniversary">
  <svg viewBox="0 0 280 280">
    <circle class="frame" cx="146" cy="142" r="112"/>
    <circle class="frame" cx="146" cy="144" r="116"/>
    <path class="ornament" role="img" aria-label="Leaf sprig on the upper right of the ring"
      d="M200 40A112 112 0 0 1 248 90"/>
    <path class="ornament" role="img" aria-label="Leaf sprig on the lower left of the ring"
      d="M48 190A112 112 0 0 0 90 240"/>
  </svg>
  <div class="greeting" style="top:118px;font-size:24px;">Happy<br>Anniversary</div>
</div>

</body>
</html>
```